Business Card Design Project

Beam Clinic Hub

Dr Lomen Priscu M.D, F.R.C.S
Vascular and Vein Surgery

47-15 Quillford Avenue, Suite 318
Astoria
NY 11103

212-555-0183
718-555-0146
www.mendorapro.us back of the card for scheduled appointments up to 5 appointment dates

Target Market(s)

Male and Female patients from 25 onwards with spider veins or varicose veins

Industry/Entity Type

Business

Font styles to use
Serif

Colors
86cae6
85abd2
0456a4

Requirements
Must have
• Modern Sophisticated design using light blue and grey text
Should not have
• hearts or flowers

```html
<!DOCTYPE html>
<html lang="en">
<head>
<meta charset="utf-8">
<title>Beam Clinic Hub – Business Cards</title>
<link href="https://fonts.googleapis.com/css2?family=Libre+Baskerville:wght@400;700&display=swap" rel="stylesheet">
<style>
  :root {
    --brand-blue: #0456a4;
    --brand-blue-light: #1f6fbe;
    --sky: #86cae6;
    --mist: #85abd2;
    --paper: #ffffff;
    --panel: #f3f4f6;
    --grey-text: #4a4f57;
    --dots: #9aa0a8;
    --backdrop: #e9ebee;
  }
  * { box-sizing: border-box; margin: 0; padding: 0; }
  html, body {
    width: 1200px; height: 1023px; overflow: hidden;
    background: var(--backdrop);
    font-family: "Libre Baskerville", Georgia, serif;
  }
  .card {
    position: absolute; left: 232px;
    width: 736px; height: 420px;
    border-radius: 4px; overflow: hidden;
    box-shadow: 0 6px 18px rgba(0,0,0,.18);
  }
  /* Back: appointments */
  .card-back {
    top: 52px;
    background: linear-gradient(160deg, var(--brand-blue-light), var(--brand-blue));
    color: var(--paper);
  }
  .appt-title {
    text-align: center; font-size: 19px; letter-spacing: 1px;
    margin-top: 22px;
  }
  .appt-panel {
    position: absolute; left: 52px; right: 52px; top: 64px; height: 218px;
    background: linear-gradient(180deg, var(--paper), var(--panel));
    border: 2px solid var(--mist); border-radius: 10px;
    padding: 20px 30px 0;
    color: var(--grey-text); font-size: 13px;
  }
  .appt-row {
    display: flex; align-items: baseline; gap: 6px;
    height: 38px;
  }
  .appt-row .fill { flex: 1; border-bottom: 1px dotted var(--dots); }
  .appt-row .fill.short { flex: 0 0 170px; }
  .back-footer {
    position: absolute; left: 52px; right: 52px; bottom: 30px;
    display: flex; align-items: flex-end;
    font-size: 14px; line-height: 1.55;
  }
  .hours { flex: 1; }
  .divider {
    width: 1px; height: 56px; background: rgba(255,255,255,.6);
    margin: 0 26px;
  }
  .back-address { width: 250px; }

  /* Front: identity */
  .card-front { top: 551px; background: var(--paper); }
  .front-top {
    height: 240px; display: flex; align-items: center; justify-content: center; gap: 16px;
  }
  .brand-name {
    font-size: 42px; font-weight: 700; color: var(--brand-blue); letter-spacing: 1px;
  }
  .brand-dot {
    width: 18px; height: 18px; border-radius: 50%; background: var(--sky);
  }
  .stripe { height: 12px; background: var(--sky); }
  .front-bottom {
    position: absolute; left: 0; right: 0; bottom: 0; top: 252px;
    background: linear-gradient(160deg, var(--brand-blue-light), var(--brand-blue));
    color: var(--paper);
    display: flex; align-items: center; padding: 0 40px;
  }
  .identity { flex: 1; }
  .doctor-name { font-size: 19px; margin-bottom: 8px; }
  .specialty { font-size: 14px; color: #e4eef8; }
  .front-bottom .divider { height: 100px; margin: 0 36px 0 20px; }
  .contact { width: 300px; font-size: 14px; line-height: 1.5; }
  .contact-address { margin-bottom: 10px; }
  .contact-line { display: flex; align-items: center; gap: 8px; }
  .contact-line svg { width: 15px; height: 15px; flex: none; }
</style>
</head>
<body>

<section class="card card-back">
  <h2 class="appt-title">APPOINTMENTS</h2>
  <div class="appt-panel">
    <div class="appt-row"><span>Date</span><span class="fill"></span><span>Time</span><span class="fill short"></span></div>
    <div class="appt-row"><span>Date</span><span class="fill"></span><span>Time</span><span class="fill short"></span></div>
    <div class="appt-row"><span>Date</span><span class="fill"></span><span>Time</span><span class="fill short"></span></div>
    <div class="appt-row"><span>Date</span><span class="fill"></span><span>Time</span><span class="fill short"></span></div>
    <div class="appt-row"><span>Date</span><span class="fill"></span><span>Time</span><span class="fill short"></span></div>
  </div>
  <div class="back-footer">
    <div class="hours">Hours<br>Monday to Saturday - 9:00am to 5:00pm</div>
    <div class="divider"></div>
    <div class="back-address">47-15 Quillford Avenue, Suite 318<br>Astoria, NY 11103</div>
  </div>
</section>

<section class="card card-front">
  <div class="front-top">
    <span class="brand-name">Beam Clinic Hub</span>
    <span class="brand-dot"></span>
  </div>
  <div class="stripe"></div>
  <div class="front-bottom">
    <div class="identity">
      <div class="doctor-name">Dr Lomen Priscu M.D, F.R.C.S</div>
      <div class="specialty">Vascular and Vein Surgery</div>
    </div>
    <div class="divider"></div>
    <div class="contact">
      <div class="contact-address">47-15 Quillford Avenue, Suite 318<br>Astoria, NY 11103</div>
      <div class="contact-line">
        <svg viewBox="0 0 16 16"><circle cx="8" cy="8" r="8" fill="#fff"/><path d="M4.5 6c0-1 1-1.6 3.5-1.6S11.5 5 11.5 6l-1.2.6-.8-1H6.5l-.8 1zM5.5 7.5h5l.6 3.8H4.9z" fill="#0456a4"/></svg>
        <span>212-555-0183</span>
      </div>
      <div class="contact-line">
        <svg viewBox="0 0 16 16"><circle cx="8" cy="8" r="8" fill="#fff"/><rect x="5.5" y="3.5" width="5" height="9" rx="1" fill="#0456a4"/><rect x="6.3" y="4.6" width="3.4" height="5.6" fill="#fff"/></svg>
        <span>718-555-0146</span>
      </div>
      <div class="contact-line">
        <svg viewBox="0 0 16 16"><circle cx="8" cy="8" r="8" fill="#fff"/><g fill="none" stroke="#0456a4" stroke-width="1"><circle cx="8" cy="8" r="4.5"/><ellipse cx="8" cy="8" rx="2" ry="4.5"/><path d="M3.5 8h9"/></g></svg>
        <span>www.mendorapro.us</span>
      </div>
    </div>
  </div>
</section>

</body>
</html>
```